Investment Advisor E-Newsletter Banner Design

I need a banner designed for an email newsletter that will be sent monthly to clients and prospects. We want to see designs that are elegant and use our logo well. The banner should be 922x150px and should go well with the www.tlvbanda.com website. Should include Logo and email and phone number.

Target Market(s)

High net worth investors

Number of Pages Required

1 page

Requirements
Must have
• logo, place for email (info@tlvbanda.com) and phone number (415-297-6180), colors and design that work well with www.tlvbanda.com website

```html
<!DOCTYPE html>
<html lang="en">
<head>
<meta charset="utf-8">
<title>Tolvan Bay Advisors — E-Newsletter Banner</title>
<link rel="stylesheet" href="https://fonts.googleapis.com/css2?family=Montserrat:wght@500;600&display=swap">
<style>
  :root {
    --page-bg: #ececec;
    --banner-white: #ffffff;
    --brand-navy: #14129a;
    --blue-top: #4747d2;
    --blue-bottom: #15109c;
    --swoosh-light: #7a7a7a;
    --swoosh-dark: #121212;
    --icon-disc: #2a2790;
    --text-light: #ffffff;
    --divider: rgba(255, 255, 255, 0.45);
  }
  html, body {
    margin: 0;
    padding: 0;
    width: 1200px;
    height: 1200px;
    overflow: hidden;
    background: var(--page-bg);
    font-family: "Montserrat", Arial, sans-serif;
  }
  .canvas {
    position: relative;
    width: 1200px;
    height: 1200px;
  }
  .banner {
    position: absolute;
    left: 47px;
    top: 510px;
    width: 1106px;
    height: 180px;
    background: var(--banner-white);
    overflow: hidden;
  }
  .banner__shapes {
    position: absolute;
    inset: 0;
    width: 1106px;
    height: 180px;
  }
  .brand {
    position: absolute;
    left: 30px;
    top: 0;
    height: 180px;
    width: 310px;
    display: flex;
    align-items: center;
    gap: 12px;
  }
  .brand__mark {
    width: 34px;
    height: 34px;
    flex: none;
    background: var(--brand-navy);
  }
  .brand__name {
    font-size: 23px;
    font-weight: 600;
    color: var(--brand-navy);
    letter-spacing: 0;
    white-space: nowrap;
  }
  .banner__title {
    position: absolute;
    left: 456px;
    top: 70px;
    margin: 0;
    font-size: 30px;
    line-height: 38px;
    font-weight: 500;
    color: var(--text-light);
    letter-spacing: 0.3px;
  }
  .banner__divider {
    position: absolute;
    left: 736px;
    top: 55px;
    width: 1px;
    height: 72px;
    background: var(--divider);
  }
  .contact {
    position: absolute;
    left: 756px;
    top: 50px;
    margin: 0;
    padding: 0;
    list-style: none;
  }
  .contact__item {
    display: flex;
    align-items: center;
    height: 42px;
    color: var(--text-light);
    font-size: 26px;
    font-weight: 500;
    letter-spacing: 0.2px;
    white-space: nowrap;
  }
  .contact__icon {
    width: 32px;
    height: 32px;
    margin-right: 14px;
    flex: none;
  }
</style>
</head>
<body>
<div class="canvas">
  <header class="banner">
    <svg class="banner__shapes" viewBox="0 0 1106 180" aria-hidden="true">
      <defs>
        <linearGradient id="swooshFill" x1="0" y1="0" x2="0" y2="1">
          <stop offset="0" stop-color="var(--swoosh-light)"/>
          <stop offset="1" stop-color="var(--swoosh-dark)"/>
        </linearGradient>
        <linearGradient id="panelFill" x1="0" y1="0" x2="0" y2="1">
          <stop offset="0" stop-color="var(--blue-top)"/>
          <stop offset="1" stop-color="var(--blue-bottom)"/>
        </linearGradient>
      </defs>
      <path d="M448 0 Q372 8 368 92 Q366 150 414 180 L470 180 L470 0 Z" fill="url(#swooshFill)"/>
      <path d="M500 0 Q406 4 398 88 Q396 150 458 180 L1106 180 L1106 0 Z" fill="url(#panelFill)"/>
    </svg>

    <div class="brand">
      <span class="brand__mark"></span>
      <span class="brand__name">Tolvan Bay Advisors</span>
    </div>

    <h1 class="banner__title">E-NEWSLETTER</h1>
    <span class="banner__divider"></span>

    <ul class="contact">
      <li class="contact__item">
        <svg class="contact__icon" viewBox="0 0 32 32" aria-hidden="true">
          <circle cx="16" cy="16" r="16" fill="var(--icon-disc)"/>
          <path d="M11.6 9.5c.5-.4 1.2-.3 1.5.2l1.5 2.4c.3.5.2 1.1-.2 1.4l-1 .8c.7 1.6 2 2.9 3.6 3.7l.8-1c.4-.4 1-.5 1.4-.2l2.4 1.5c.5.3.6 1 .2 1.5l-1 1.2c-.6.7-1.6.9-2.5.6-3.7-1.4-6.6-4.3-8-8-.3-.9-.1-1.9.6-2.5z" fill="#ffffff"/>
        </svg>
        <span>415-297-6180</span>
      </li>
      <li class="contact__item">
        <svg class="contact__icon" viewBox="0 0 32 32" aria-hidden="true">
          <circle cx="16" cy="16" r="16" fill="var(--icon-disc)"/>
          <rect x="9.5" y="11.5" width="13" height="9.5" rx="1" fill="#ffffff"/>
          <path d="M9.8 12.2 16 16.6 22.2 12.2" fill="none" stroke="var(--icon-disc)" stroke-width="1.3"/>
        </svg>
        <span>info@tlvbanda.com</span>
      </li>
    </ul>
  </header>
</div>
</body>
</html>
```